Kestrada LLC, needs a web page no more than 5 pages (for now)

Kestrada is a general contractor. Our services include general contracting, design-build construction, disaster recovery and environmental remediation. Our main clients are PMX, TQ, State and Local Gov't Agencies, Hospitals and Schools. Kestrada is also a SDVOSB.

```html
<!DOCTYPE html>
<html lang="en">
<head>
<meta charset="UTF-8">
<title>Kestrada LLC — General Contractor</title>
<link rel="stylesheet" href="https://fonts.googleapis.com/css2?family=League+Spartan:wght@500;600;700&family=Poppins:wght@400;500;600&display=swap">
<style>
:root{
  --gold-1:#e4c971;
  --gold-2:#b98f2f;
  --gold:#c9a44a;
  --gold-text:#c09530;
  --ink:#111111;
  --body:#555555;
  --muted:#8a8a8a;
  --black:#000000;
  --white:#ffffff;
  --line:#e3e3e3;
  --gold-grad:linear-gradient(180deg,var(--gold-1),var(--gold-2));
}
*{box-sizing:border-box;margin:0;padding:0}
html,body{width:1200px;height:4870px;overflow:hidden;background:var(--white)}
body{position:relative;font-family:"Poppins",sans-serif;color:var(--ink)}
.abs{position:absolute}
.heading{font-family:"League Spartan",sans-serif;font-weight:600;color:var(--ink);line-height:1}
.eyebrow{font-family:"Poppins",sans-serif;font-size:21px;letter-spacing:1.5px;color:var(--gold-text);display:flex;align-items:center;gap:12px;text-transform:uppercase}
.eyebrow::after{content:"";width:42px;height:2px;background:var(--gold)}
.eyebrow.both::before{content:"";width:42px;height:2px;background:var(--gold)}
.btn{display:flex;align-items:center;justify-content:center;font-weight:600;text-transform:uppercase;color:var(--ink);background:var(--gold-grad);border-radius:18px 4px 18px 4px;box-shadow:0 4px 8px rgba(0,0,0,.18)}
.photo{background:linear-gradient(135deg,#8d8a84,#c9b79a 55%,#6d6559)}
.brand{font-family:"League Spartan",sans-serif;font-weight:600;color:var(--gold-text);display:flex;align-items:center;gap:10px;letter-spacing:2px}
.brand .dot{width:16px;height:16px;border-radius:50%;background:var(--gold)}

/* header */
.site-header{top:0;left:0;width:1200px;height:134px}
.site-header .brand{left:66px;top:48px;font-size:34px}
.contact-chip{display:flex;gap:10px;align-items:center;font-size:13px;line-height:16px;color:var(--ink)}
.chip-icon{width:28px;height:28px;border-radius:6px;background:var(--gold-grad);display:flex;align-items:center;justify-content:center}
.contact-chip b{font-weight:600;display:block}
.nav{top:88px;left:572px;display:flex;gap:0;font-size:13px;color:#333}
.nav a{text-decoration:none;color:inherit;height:30px;display:flex;align-items:flex-start}
.nav a.active{color:var(--gold-text);border-bottom:2px solid var(--gold)}

/* hero */
.hero{top:134px;left:0;width:1200px;height:811px;overflow:hidden}
.hero-photo{position:absolute;inset:0;background:linear-gradient(100deg,#caa86a 0%,#9c8a70 30%,#7d7a76 55%,#b9b3aa 80%,#d8d3cb 100%)}
.hero-panel{position:absolute;left:582px;top:178px;width:640px;height:378px;background:rgba(40,36,30,.72);border-radius:34px 0 0 34px;padding:50px 0 0 63px;color:var(--white)}
.hero-panel h1{font-family:"League Spartan",sans-serif;font-weight:600;font-size:56px;line-height:63px;color:var(--white)}
.hero-panel p{font-size:15px;line-height:27px;margin-top:12px;width:490px;color:#eee}
.hero-btns{display:flex;gap:15px;margin-top:28px}
.hero-btns .btn{width:213px;height:64px;font-size:18px}
.btn.outline{background:transparent;border:2px solid var(--gold);color:var(--gold-1);box-shadow:none}
.hero-dots{position:absolute;left:571px;top:695px;display:flex;gap:4px}
.hero-dots span{width:10px;height:10px;border-radius:50%;background:#ddd}
.hero-dots span:first-child{background:#fff}
.hero-curve{position:absolute;left:0;top:700px}

/* about */
.about .eyebrow{left:128px;top:1068px}
.about h2{left:128px;top:1102px;font-size:60px}
.about .lead{left:125px;top:1196px;width:460px;font-size:16px;font-weight:600;line-height:27px;color:var(--ink)}
.about .body{left:125px;top:1295px;width:460px;font-size:13px;line-height:26.5px;color:var(--body)}
.about .btn{left:125px;top:1517px;width:215px;height:63px;font-size:19px}
.framed{background:var(--white);border-radius:70px 0 70px 0;box-shadow:0 4px 18px rgba(0,0,0,.15);padding:14px}
.framed .photo{width:100%;height:100%;border-radius:60px 0 60px 0}

/* services */
.services .eyebrow{left:0;width:1200px;justify-content:center;top:1724px}
.services h2{left:0;width:1200px;text-align:center;top:1752px;font-size:60px}
.services .intro{left:0;width:1200px;text-align:center;top:1851px;font-size:13.5px;line-height:27px;color:var(--body)}
.card{width:522px;height:495px;background:var(--white);box-shadow:0 2px 10px rgba(0,0,0,.13);text-align:center}
.card .photo{height:259px}
.card h3{font-family:"League Spartan",sans-serif;font-weight:600;font-size:28px;margin-top:24px;text-transform:uppercase;letter-spacing:.3px}
.card p{font-size:13.5px;line-height:27px;color:var(--body);width:470px;margin:10px auto 0}
.card .btn{width:137px;height:32px;font-size:11px;margin:20px auto 0;border-radius:12px 3px 12px 3px}

/* testimonials */
.testimonials .eyebrow{left:68px;top:3222px}
.testimonials h2{left:68px;top:3254px;font-size:60px}
.avatar{left:444px;top:3266px;width:132px;height:132px;border-radius:50%;background:linear-gradient(160deg,#d9d9d9,#7e8a99);border:6px solid var(--white);box-shadow:0 3px 10px rgba(0,0,0,.25);z-index:2}
.slider-arrow{width:40px;height:40px;border-radius:50%;display:flex;align-items:center;justify-content:center}
.quote-panel{left:505px;top:3141px;width:695px;height:369px;background:linear-gradient(180deg,var(--gold-1),var(--gold-2));border-radius:80px 0 0 0;text-align:center}
.quote-panel p{position:absolute;left:103px;top:122px;width:526px;font-size:14px;line-height:29px;text-align:justify;color:#2a2210}
.quote-panel .role{position:absolute;left:0;width:100%;top:256px;font-size:14px;color:#2a2210}
.quote-panel .name{position:absolute;left:0;width:100%;top:286px;font-family:"League Spartan",sans-serif;font-size:23px;font-weight:600;letter-spacing:1px;color:#2a2210}

/* contact */
.contact .eyebrow{left:618px;top:3728px}
.contact h2{left:618px;top:3760px;font-size:60px}
.field{background:var(--white);border:1px solid var(--line);box-shadow:0 1px 4px rgba(0,0,0,.08);font-size:12.5px;color:var(--muted);padding:14px 20px}
.contact .btn{left:624px;top:4162px;width:213px;height:62px;font-size:19px}

/* footer */
.footer-curve{left:0;top:4380px}
.site-footer{left:0;top:4490px;width:1200px;height:380px;background:var(--black);color:var(--white)}
.site-footer .brand{left:85px;top:118px;font-size:46px}
.foot-col h4{font-family:"League Spartan",sans-serif;font-weight:600;font-size:19px;color:var(--white)}
.foot-col h4 span{color:var(--gold-1)}
.foot-col ul{list-style:none;margin-top:28px;font-size:13px;line-height:26px}
.foot-col li{display:flex;align-items:center;gap:12px}
.foot-col li::before{content:"";width:8px;height:8px;border-radius:50%;background:var(--gold)}
.foot-contact{display:flex;gap:15px;font-size:13px;line-height:17px;margin-top:18px}
.foot-contact .chip-icon{flex:none;width:26px;height:26px}
.social{display:flex;gap:6px}
.social span{width:26px;height:26px;border-radius:50%;background:var(--gold-grad)}
</style>
</head>
<body>

<header class="abs site-header">
  <div class="abs brand"><span class="dot"></span>KESTRADA</div>
  <div class="abs contact-chip" style="left:758px;top:36px">
    <span class="chip-icon"><svg width="14" height="14" viewBox="0 0 24 24"><path d="M6.6 10.8a15 15 0 006.6 6.6l2.2-2.2a1 1 0 011-.25 11.4 11.4 0 003.6.57 1 1 0 011 1V20a1 1 0 01-1 1A17 17 0 013 4a1 1 0 011-1h3.5a1 1 0 011 1c0 1.25.2 2.45.57 3.57a1 1 0 01-.25 1z" fill="#fff"/></svg></span>
    <div><b>Call Us</b>012 555 0147</div>
  </div>
  <div class="abs contact-chip" style="left:928px;top:36px">
    <span class="chip-icon"><svg width="14" height="12" viewBox="0 0 24 18"><rect x="1" y="1" width="22" height="16" rx="2" fill="#fff"/><path d="M2 2l10 8 10-8" stroke="#b98f2f" stroke-width="2" fill="none"/></svg></span>
    <div><b>Email Us</b>hello@kestrada-build.com</div>
  </div>
  <nav class="abs nav">
    <a class="active" href="#" style="padding:0 10px">HOME</a>
    <a href="#" style="margin-left:69px">ABOUT US</a>
    <a href="#" style="margin-left:56px">SERVICES ▾</a>
    <a href="#" style="margin-left:48px">CLIENTS</a>
    <a href="#" style="margin-left:56px">CONTACT US</a>
  </nav>
</header>

<section class="abs hero">
  <div class="hero-photo" role="img" aria-label="Two construction professionals in hard hats reviewing plans on site"></div>
  <div class="hero-panel">
    <h1>We Build Something<br>New And Consistent</h1>
    <p>Lorem ipsum dolor sit amet, consectetur adipiscing elit, sed do eiusmod tempor incididunt ut labore et .</p>
    <div class="hero-btns">
      <a class="btn">Get Start</a>
      <a class="btn outline">Our Services</a>
    </div>
  </div>
  <div class="hero-dots"><span></span><span></span><span></span><span></span></div>
  <svg class="hero-curve" width="1200" height="111" viewBox="0 0 1200 111">
    <path d="M0 40 Q600 200 1200 30 L1200 111 L0 111Z" fill="url(#heroGold)"/>
    <path d="M0 30 Q600 140 1200 10 L1200 111 L0 111Z" fill="#fff"/>
    <path d="M0 60 Q600 190 1200 50 Q600 150 0 60Z" fill="url(#heroGold)"/>
    <defs><linearGradient id="heroGold" x1="0" x2="1"><stop offset="0" stop-color="#b98f2f"/><stop offset=".5" stop-color="#e4c971"/><stop offset="1" stop-color="#b98f2f"/></linearGradient></defs>
  </svg>
</section>

<section class="about">
  <div class="abs eyebrow">Who We Are</div>
  <h2 class="abs heading">About Us</h2>
  <p class="abs lead">Lorem ipsum dolor sit amet, consectetur adipiscing elit. Aenean semper nunc urna, sit amet lobortis erat scelerisque sit amet.</p>
  <p class="abs body" style="text-align:justify">Lorem ipsum dolor sit amet, consectetur adipiscing elit, sed do ei usmod tempor incididunt ut labore et dolore magna aliqua. Ut enim ad minim veniam, quis nostrud exercitation ullamco laboris nisi ut aliquip ex ea commodo consequat. Duis aute irure dolor in reprehenderit in voluptate velit esse cillum dolore eu fugiat nulla pariatur. Excepteur sint occaecat cupidatat non proident, sunt in culpa qui officia .</p>
  <a class="abs btn">Read More</a>
  <div class="abs framed" style="left:646px;top:1071px;width:431px;height:509px">
    <div class="photo" role="img" aria-label="Site engineer and manager studying blueprints at a construction site"></div>
  </div>
</section>

<section class="services">
  <div class="abs eyebrow both">What We Do</div>
  <h2 class="abs heading">Our Services</h2>
  <p class="abs intro">Lorem ipsum dolor sit amet, consectetur adipiscing elit, sed do ei usmod tempor incididunt ut labore et dolore magna aliqua.<br>Ut enim ad minim veniam, quis nostrud exercitation ullamco laboris nisi ut aliquip ex ea commodo consequat.</p>

  <article class="abs card" style="left:66px;top:1962px">
    <div class="photo" role="img" aria-label="Contractor in safety vest reading plans beside a building under construction" style="background:linear-gradient(135deg,#6f7b8a,#b7a48a 55%,#d78a2c)"></div>
    <h3>General Contracting</h3>
    <p>Lorem ipsum dolor sit amet, consectetur adipiscing elit. Praesent erat sem, placerat at placerat a, facilisis eget mauris. Nunc luctus nunc lorem, ac posu ere sem feugiat eu.</p>
    <a class="btn">Read More</a>
  </article>
  <article class="abs card" style="left:610px;top:1962px">
    <div class="photo" role="img" aria-label="Architect's desk with house model, drawings and pen" style="background:linear-gradient(135deg,#f1efea,#cfd3d6 50%,#9aa6b0)"></div>
    <h3>Design-Build Construction</h3>
    <p>Lorem ipsum dolor sit amet, consectetur adipiscing elit. Praesent erat sem, placerat at placerat a, facilisis eget mauris. Nunc luctus nunc lorem, ac posu ere sem feugiat eu.</p>
    <a class="btn">Read More</a>
  </article>
  <article class="abs card" style="left:66px;top:2497px">
    <div class="photo" role="img" aria-label="Aerial view of damaged abandoned buildings among bare trees" style="background:linear-gradient(135deg,#9aa0a3,#7a6a58 55%,#5c4f43)"></div>
    <h3>Disaster Recovery</h3>
    <p>Lorem ipsum dolor sit amet, consectetur adipiscing elit. Praesent erat sem, placerat at placerat a, facilisis eget mauris. Nunc luctus nunc lorem, ac posu ere sem feugiat eu.</p>
    <a class="btn">Read More</a>
  </article>
  <article class="abs card" style="left:610px;top:2497px">
    <div class="photo" role="img" aria-label="Workers in safety vests clearing brush and soil outdoors" style="background:linear-gradient(135deg,#3f5a2e,#6e7a3c 50%,#c86a2a)"></div>
    <h3>Environmental Remediation</h3>
    <p>Lorem ipsum dolor sit amet, consectetur adipiscing elit. Praesent erat sem, placerat at placerat a, facilisis eget mauris. Nunc luctus nunc lorem, ac posu ere sem feugiat eu.</p>
    <a class="btn">Read More</a>
  </article>
</section>

<section class="testimonials">
  <div class="abs eyebrow">Client Reviews</div>
  <h2 class="abs heading">Testimonials</h2>
  <div class="abs slider-arrow" style="left:314px;top:3459px;background:#d4d4d4"><svg width="14" height="10" viewBox="0 0 14 10"><path d="M13 5H2M5 1L1 5l4 4" stroke="#fff" stroke-width="1.6" fill="none"/></svg></div>
  <div class="abs slider-arrow" style="left:364px;top:3459px;background:#000"><svg width="14" height="10" viewBox="0 0 14 10"><path d="M1 5h11M9 1l4 4-4 4" stroke="#fff" stroke-width="1.6" fill="none"/></svg></div>
  <div class="abs quote-panel">
    <svg class="abs" style="left:351px;top:52px" width="50" height="40" viewBox="0 0 50 40"><path d="M0 40V22C0 9 7 2 19 0l2 6c-6 2-9 6-9 12h10v22zM28 40V22C28 9 35 2 47 0l2 6c-6 2-9 6-9 12h10v22z" fill="#111"/></svg>
    <p>Lorem ipsum dolor sit amet, conse ctetuer adipiscing elit. Aenean comodo ligula eget dolor. Aenean massa. Cum sociis natoque pen atibus et magnis dis parturient montes, nascetur ridiculus mus. Donec quam felis, ultricies nec, pell entesque eu, pretium quis, sem. Nulla</p>
    <div class="role">Happy Clients</div>
    <div class="name">MARCUS HALE</div>
  </div>
  <div class="abs avatar" role="img" aria-label="Client portrait"></div>
</section>

<section class="contact">
  <div class="abs framed" style="left:113px;top:3729px;width:431px;height:510px">
    <div class="photo" role="img" aria-label="Smiling engineer in hard hat holding rolled plans in front of buildings" style="background:linear-gradient(135deg,#9fb4c8,#d8d2c6 50%,#2e3440)"></div>
  </div>
  <div class="abs eyebrow">Get In Touch</div>
  <h2 class="abs heading">Contact Us</h2>
  <div class="abs field" style="left:618px;top:3861px;width:221px;height:43px">First Name:</div>
  <div class="abs field" style="left:860px;top:3861px;width:221px;height:43px">Last Name:</div>
  <div class="abs field" style="left:618px;top:3925px;width:221px;height:44px">Phone:</div>
  <div class="abs field" style="left:860px;top:3925px;width:221px;height:44px">Email:</div>
  <div class="abs field" style="left:618px;top:3992px;width:463px;height:139px;padding-top:24px">Mesoge:</div>
  <a class="abs btn">Submit Now</a>
</section>

<svg class="abs footer-curve" width="1200" height="120" viewBox="0 0 1200 120">
  <defs><linearGradient id="footGold" x1="0" x2="1"><stop offset="0" stop-color="#b98f2f"/><stop offset=".5" stop-color="#e4c971"/><stop offset="1" stop-color="#b98f2f"/></linearGradient></defs>
  <path d="M0 115 Q600 -40 1200 115 Q600 0 0 115Z" fill="url(#footGold)"/>
  <path d="M0 120 Q600 10 1200 120Z" fill="#000"/>
</svg>

<footer class="abs site-footer">
  <div class="abs brand"><span class="dot"></span>KESTRADA</div>
  <div class="abs foot-col" style="left:391px;top:48px">
    <h4>Quick <span>Links</span></h4>
    <ul><li>About Us</li><li>Services</li><li>Clients</li><li>Contact Us</li></ul>
  </div>
  <div class="abs foot-col" style="left:618px;top:48px">
    <h4>Contact <span>Us</span></h4>
    <div class="foot-contact" style="margin-top:34px"><span class="chip-icon"><svg width="12" height="12" viewBox="0 0 24 24"><path d="M6.6 10.8a15 15 0 006.6 6.6l2.2-2.2a1 1 0 011-.25 11.4 11.4 0 003.6.57 1 1 0 011 1V20a1 1 0 01-1 1A17 17 0 013 4a1 1 0 011-1h3.5a1 1 0 011 1c0 1.25.2 2.45.57 3.57a1 1 0 01-.25 1z" fill="#fff"/></svg></span><div>CALL US<br>012 555 0147</div></div>
    <div class="foot-contact"><span class="chip-icon"><svg width="12" height="10" viewBox="0 0 24 18"><rect x="1" y="1" width="22" height="16" rx="2" fill="#fff"/><path d="M2 2l10 8 10-8" stroke="#b98f2f" stroke-width="2" fill="none"/></svg></span><div>EMAIL US<br>hello@kestrada-build.com</div></div>
    <div class="foot-contact"><span class="chip-icon"><svg width="10" height="13" viewBox="0 0 20 26"><path d="M10 0a10 10 0 00-10 10c0 7 10 16 10 16s10-9 10-16A10 10 0 0010 0zm0 14a4 4 0 110-8 4 4 0 010 8z" fill="#fff"/></svg></span><div>Address line Dummy here<br>Address line dummy</div></div>
  </div>
  <div class="abs foot-col" style="left:922px;top:48px">
    <h4>Our <span>Newsletter</span></h4>
    <p style="font-size:12.5px;line-height:16px;margin-top:30px;width:220px">Subscribe our newsletter to get the latest news.</p>
    <div style="width:196px;height:31px;background:#fff;margin-top:16px"></div>
    <a class="btn" style="width:98px;height:26px;font-size:9px;margin-top:20px;border-radius:10px 3px 10px 3px">Subscribe</a>
  </div>
  <div class="abs" style="left:66px;top:340px;font-size:11px;color:#ddd">Copyright © 2025 All Rights Reserved By Kestrada LLC</div>
  <div class="abs social" style="left:1010px;top:334px"><span></span><span></span><span></span><span></span></div>
</footer>

</body>
</html>
```